Visitenkarten/Briefpaier/Kassenkassenbelege für Juwelier
Zielgruppe
Mittelständischer Juwelier mit zwei Filialen. Klassischer Schmuck, Uhren und Modeschmuck
Aufgabenstellung
Es müssen für zwei Geschäfte Visitenkarten, Briefpapier (A4) und Kassenkassenbelege (A6) erstellt werden. Logo und Typo im Anhang. Ein Farbkonzept besteht noch nicht. Die Idee geht in Richtung Bordeaux-Rot.
Generell:
(1) Sieht erstmal nach viel Beschreibung aus, bitte nicht entmutigen lassen, sind zu 90% nur austauschbare Inhalts-/Kontaktdaten.
(2) Für meine Zwecke reicht es vollkommen aus, wenn bei den Vorschlägen zur Arbeitsersparnis erstmal nur mit einer Adresse gearbeitet wird. Wenn ich dann den zutreffenden Designvorschlag gefunden habe, können wir die zweite Adresse in dem ersten Format umsetzen. Ich denke das spart Zeit und Nerven.
(3) Bitte Angaben wie "Tel.:" oder "USt.- ID:" nicht wörtlich nehmen, es soll dabei klar sein worum es geht; wenn "Telefon" ausgeschrieben besser aussieht, bitte in der optisch ansprechenderen Form verwenden.
(4) Bei Fragen, bitte fragen!
(5) Viel Spass bei dem Projekt - Ich freu' mich auf die Vorschläge!
Visitenkarten(1):
Juwelier Brenneck GmbH
www.juwelier-brenneck-beispiel.de
Visitenkarten(2):
Visitenkarten(generell):
(1) Die einzelnen Daten können durch Hervorhebungen wie Adresse, Kontakt, Online/Internet unterteilt bzw. hervorgehoben werden.
(2) Die Visitenkarten sollen farbig gedruckt werden; geplant ist weiß als Hintergrund ist aber nicht zwingend bei einer guten anderen Idee
Briefpapier:
(1)Absender im Adressfeld für DIN-lang Briefumschläge mit Fenster:
(2)Informationen im Footer/Seitenbereich:
Juwelier Brenneck Gmb..

```html
<!DOCTYPE html>
<html lang="de">
<head>
<meta charset="utf-8">
<title>Juwelier Brenneck – Visitenkarte</title>
<link href="https://fonts.googleapis.com/css2?family=Source+Sans+3:wght@400;600&display=swap" rel="stylesheet">
<style>
  :root {
    --bordeaux: #6b1642;
    --stone: #a4a6a2;
    --paper: #ffffff;
    --backdrop: #e9e9e7;
    --ink-grey: #8e908c;
  }
  * { margin: 0; padding: 0; box-sizing: border-box; }
  html, body { width: 1200px; height: 800px; overflow: hidden; }
  body {
    background: var(--backdrop);
    font-family: "Source Sans 3", "Source Sans Pro", sans-serif;
    position: relative;
  }
  .card {
    position: absolute;
    top: 235px;
    width: 510px;
    height: 330px;
    box-shadow: 0 8px 28px rgba(0,0,0,.12);
  }
  .card--front { left: 60px; background: var(--bordeaux); }
  .card--back { left: 630px; background: var(--paper); }

  .edge-tab {
    position: absolute;
    right: 0;
    width: 38px;
    height: 52px;
    background: var(--stone);
  }
  .card--front .edge-tab { bottom: 44px; }
  .card--back .edge-tab { top: 139px; }

  .front-brand {
    position: absolute;
    left: 0; right: 0;
    top: 118px;
    display: flex;
    align-items: center;
    justify-content: center;
    gap: 18px;
  }
  .brand-square {
    width: 56px; height: 56px;
    background: var(--paper);
  }
  .brand-name {
    color: var(--stone);
    font-weight: 600;
    font-size: 36px;
    letter-spacing: 1px;
    text-transform: uppercase;
  }
  .front-rule {
    position: absolute;
    left: 118px; right: 118px;
    top: 204px;
    height: 1px;
    background: var(--stone);
  }

  .back-mark {
    position: absolute;
    left: 250px; top: 38px;
    width: 46px; height: 46px;
    background: var(--stone);
  }
  .back-mark::after {
    content: "";
    position: absolute;
    left: 14px; top: 10px;
    width: 38px; height: 30px;
    background: var(--bordeaux);
  }
  .contact {
    position: absolute;
    right: 62px;
    top: 110px;
    text-align: right;
    font-size: 17px;
    line-height: 1.42;
    color: var(--bordeaux);
  }
  .contact .company {
    color: var(--ink-grey);
    text-transform: uppercase;
    letter-spacing: .5px;
  }
  .contact .label { color: var(--ink-grey); }
</style>
</head>
<body>
  <section class="card card--front">
    <div class="front-brand">
      <span class="brand-square"></span>
      <span class="brand-name">Juwelier Brenneck</span>
    </div>
    <div class="front-rule"></div>
    <div class="edge-tab"></div>
  </section>

  <section class="card card--back">
    <div class="back-mark"></div>
    <address class="contact" style="font-style:normal">
      <div class="company">Juwelier Brenneck GmbH</div>
      <div>Lindenallee 12 in 45127 Essen</div>
      <div><span class="label">TEL</span> 0201-555018 &nbsp;<span class="label">FAX</span> 0201-555019</div>
      <div>info@juwelier-brenneck-beispiel.de</div>
      <div>www.juwelier-brenneck-beispiel.de</div>
    </address>
    <div class="edge-tab"></div>
  </section>
</body>
</html>
```